Varsity Purse Wordpress Website (re)design

we are a student run financial literacy website and are desperately trying to get college students to pay attention to the finances to create solid financial skills for life. This age group LOVES pixolette so instead of sharing a lot of text we want to tease through graphics/infographics topics that are relevant to them based on what their peers are discussing and then push them to our resources to learn more. ultimately we will also recommend products to them that are carefully selected by us. these will range from a book on paying back their student loan to a place to store their dorm stuff when they go home for summer break to a credit card we determine is best for them. So yes, commerce is imp but SEO to attract students comes first which we will do through survey monkey and cash prizes. we need to capture email address. we also have a "checklist" (attached and needs rebranding) of the basic and most imp money matters for them. Each item will hyperlink to our parnter, nuvoe, and need to do so seamlessly and push them back to us.

Target Market(s)

college students and young adults

Requirements
Must have
• simple, clean and graphic with an integration of survey monkey, an borvel store and a capture of emails through mailchimp or other similar. Ability to edit after ourselves on wordpress

```html
<!DOCTYPE html>
<html lang="en">
<head>
<meta charset="utf-8">
<title>Varsity Purse — Take Charge of your Change</title>
<link href="https://fonts.googleapis.com/css2?family=Domine:wght@400;700&family=Roboto:wght@400;500;700&family=Montserrat:wght@400;500;600&display=swap" rel="stylesheet">
<style>
:root{
  --blue:#1c74b3;
  --blue-dark:#16629a;
  --green:#5cb531;
  --green-dark:#4aa02a;
  --ink:#222;
  --muted:#666;
  --line:#e6e6e6;
  --footer:#141414;
  --star:#f26b1d;
}
*{box-sizing:border-box;margin:0;padding:0}
html,body{width:1200px;height:4242px;overflow:hidden}
body{position:relative;font-family:'Roboto',sans-serif;color:var(--ink);background:#fff}
.abs{position:absolute}
.serif{font-family:'Domine',serif}

/* top bar */
.topbar{left:0;top:0;width:1200px;height:44px;background:var(--blue);color:#fff;font-size:14px}
.topbar .contact{left:90px;top:14px}
.topbar .social{right:90px;top:13px;display:flex;gap:14px}
.topbar .social span{width:16px;height:16px;border:2px solid #fff;border-radius:50%;display:block}

/* header */
.header{left:0;top:44px;width:1200px;height:173px;background:#fff}
.brand{left:90px;top:52px;display:flex;align-items:center;gap:10px}
.brand .dot{width:30px;height:30px;border-radius:50%;background:var(--green)}
.brand .name{font-family:'Roboto',sans-serif;font-size:38px;font-weight:500;color:var(--blue)}
.callus{left:723px;top:43px;font-size:18px;font-weight:700;display:flex;align-items:center;gap:8px}
.callus i{width:20px;height:20px;border-radius:50%;background:var(--green);display:block}
.btn-contact{left:970px;top:35px;width:135px;height:38px;border-radius:19px;background:var(--green);color:#fff;font-size:15px;font-weight:500;text-align:center;line-height:38px}
.nav{left:444px;top:112px;display:flex;gap:20px;font-size:15px;font-weight:500;align-items:center}
.nav .active{border:2px solid var(--green);padding:4px 12px}
.nav .dd:after{content:" ⌄";font-size:12px}

/* hero */
.hero{left:0;top:217px;width:1200px;height:740px;background:linear-gradient(120deg,#3e4a52 0%,#6b7478 45%,#8b8680 70%,#4f5558 100%)}
.hero-title{left:90px;top:460px;font-size:56px;line-height:66px;color:#fff;font-weight:400}
.hero-sub{left:92px;top:608px;font-size:20px;line-height:38px;color:#fff}
.btn-quote{left:90px;top:700px;width:256px;height:64px;border-radius:32px;background:var(--green);color:#fff;font-size:26px;font-weight:500;text-align:center;line-height:64px}
.dots{left:563px;top:818px;display:flex;gap:14px}
.dots span{width:16px;height:16px;border-radius:50%;border:2px solid #fff}
.dots .on{background:var(--green);border-color:var(--green)}

/* welcome */
.welcome{left:140px;top:1055px;width:920px;text-align:center;font-size:27px;line-height:41px}

/* feature cards */
.card{top:1225px;width:328px;height:475px;background:#fff;box-shadow:0 2px 8px rgba(0,0,0,.18);text-align:center}
.card .ph{height:200px;width:100%}
.card .icon{position:absolute;left:127px;top:175px;width:74px;height:74px;border-radius:50%;background:var(--blue);border:4px solid #fff}
.card .icon svg{margin-top:18px}
.card h3{margin-top:58px;font-size:21px;font-weight:500;line-height:27px;padding:0 30px}
.card p{margin-top:18px;font-size:15.5px;line-height:24px;color:var(--muted);padding:0 22px}
.card .more{position:absolute;left:82px;top:408px;width:164px;height:46px;border-radius:23px;background:var(--green);color:#fff;font-size:18px;font-weight:500;line-height:46px}

/* course band */
.band{left:0;top:1815px;width:1200px;height:630px;background:linear-gradient(90deg,#1f6ea6,#2d88c4 55%,#2279b5)}
.frame{left:248px;top:1877px;width:812px;height:508px;border:3px solid var(--green)}
.checklist{left:140px;top:1910px;width:322px;height:440px;background:linear-gradient(180deg,#ffffff 0%,#e4eff9 40%,#d6e7f6 100%);border:1px solid #9cc0e0}
.band h2{left:518px;top:1955px;font-size:43px;font-weight:500;line-height:55px;color:#fff}
.band .copy{left:520px;top:2075px;width:500px;font-size:17.5px;line-height:29px;color:#fff}
.band .quote{left:518px;top:2203px;width:460px;font-size:17.5px;line-height:32px;color:#fff;font-style:italic}

/* resources */
.resources{left:0;top:2445px;width:1200px;height:665px;background:linear-gradient(180deg,#f4f4f3,#ecebe9)}
.section-title{left:0;width:1200px;text-align:center;font-size:44px}
.post{background:#fff;box-shadow:0 3px 8px rgba(0,0,0,.18)}
.post .ph{position:absolute;left:0;top:0}
.post .date{position:absolute;left:0;top:0;width:56px;height:62px;background:var(--green);color:#fff;font-size:12px;padding:10px 0 0 16px;line-height:18px}
.post .date b{font-size:15px}
.post h4{font-size:16px;font-weight:700;line-height:20px}
.post .meta{font-size:13.5px;color:#444;margin-top:4px}
.post .ex{font-family:'Domine',serif;font-size:11px;color:#777;line-height:20px;margin-top:8px}
.post .rm{font-family:'Montserrat',sans-serif;font-size:16px;font-weight:600;color:var(--blue);margin-top:8px;letter-spacing:.5px}
.post .body{position:absolute}

/* reviews */
.sub{left:0;width:1200px;text-align:center;font-size:23px;color:#444}
.review{top:3362px;width:306px;height:176px;border:1px solid var(--line);box-shadow:0 3px 8px rgba(0,0,0,.14);background:#fff;text-align:center;font-family:'Montserrat',sans-serif;font-size:13px;line-height:25px;color:#777;padding:40px 28px 0}
.avatar{top:3302px;width:92px;height:92px;border-radius:50%;background:linear-gradient(160deg,#d9c2b0,#8a6a58);border:3px solid #fff}
.who{top:3578px;width:306px;text-align:center;font-family:'Montserrat',sans-serif;font-size:18px;line-height:24px;color:var(--green)}
.stars{top:3632px;width:306px;text-align:center;color:var(--star);font-size:16px;letter-spacing:4px}

/* footer */
.footer{left:0;top:3760px;width:1200px;height:482px;background:var(--footer);color:#fff;font-family:'Montserrat',sans-serif}
.footer h5{position:absolute;font-size:20px;font-weight:500}
.fitem{position:absolute;font-size:16px;line-height:24px}
.ficon{position:absolute;width:30px;height:30px;border:2px solid #fff;border-radius:50%}
.flinks{position:absolute;font-size:16px;line-height:29px}
.news-input{position:absolute;left:878px;top:4017px;width:186px;height:34px;background:#fff;color:#777;font-size:11px;line-height:34px;padding-left:8px}
.news-btn{position:absolute;left:1064px;top:4017px;width:46px;height:34px;background:var(--green)}
.copyright{position:absolute;left:0;top:4183px;width:1200px;text-align:center;font-size:18px}
</style>
</head>
<body>

<div class="abs topbar">
  <div class="abs contact">&#9743;&nbsp; 555 014 2290 &nbsp;|&nbsp; &#9993;&nbsp; hello@varsitypurse.org</div>
  <div class="abs social"><span></span><span></span><span></span><span></span></div>
</div>

<header class="abs header">
  <div class="abs brand"><span class="dot"></span><span class="name">Varsity Purse</span></div>
  <div class="abs callus"><i></i>Call Us: 555 014 2290</div>
  <div class="abs btn-contact">CONTACT US</div>
  <nav class="abs nav">
    <span class="active">Home</span><span>Take The Pledge</span>
    <span class="dd">Blog</span><span class="dd">About Us</span><span class="dd">Tips &amp; Tricks</span><span class="dd">About nuvoe</span><span>Login</span>
  </nav>
</header>

<section class="abs hero" role="img" aria-label="Students working together on laptops in a bright study hall"></section>
<svg class="abs" style="left:0;top:925px" width="1200" height="40" viewBox="0 0 1200 40"><path fill="#fff" d="M0 22 L40 16 L90 24 L150 14 L210 22 L280 12 L340 20 L420 15 L500 23 L580 13 L650 21 L730 14 L800 22 L880 12 L950 20 L1030 14 L1100 22 L1160 15 L1200 19 L1200 40 L0 40Z"/></svg>
<h1 class="abs hero-title serif">Take Charge of your<br>Change</h1>
<p class="abs hero-sub">At VP, we understand that college is really<br>the first time that you can be independent .</p>
<div class="abs btn-quote">Request Quote</div>
<div class="abs dots"><span class="on"></span><span></span><span></span></div>

<p class="abs welcome serif">Welcome to your FREE resource that will help you achieve financial independence and knowledge.Using peer-to-peer tips, personal stories and nuvoe, you can become a Varsity Purse!</p>

<article class="abs card" style="left:90px">
  <div class="ph" role="img" aria-label="Family budgeting together at a table" style="background:linear-gradient(135deg,#e9e2da,#c9b9a8)"></div>
  <div class="icon"><svg width="30" height="30" viewBox="0 0 30 30" fill="none" stroke="#fff" stroke-width="2"><rect x="6" y="4" width="18" height="22" rx="2"/><line x1="10" y1="10" x2="20" y2="10"/><line x1="10" y1="15" x2="20" y2="15"/><line x1="10" y1="20" x2="16" y2="20"/></svg></div>
  <h3>How To Budget</h3>
  <p>Having a solid budget is a fundamental building block in becoming financially independent, so here is</p>
  <div class="more">Read More</div>
</article>
<article class="abs card" style="left:432px">
  <div class="ph" role="img" aria-label="Child saving coins in a jar with a parent" style="background:linear-gradient(135deg,#ece7e1,#bfb3a5)"></div>
  <div class="icon"><svg width="30" height="30" viewBox="0 0 30 30" fill="none" stroke="#fff" stroke-width="2"><circle cx="15" cy="12" r="6"/><path d="M4 22 Q15 30 26 22"/></svg></div>
  <h3>Money Saving<br>Hacks For&nbsp; Millennials</h3>
  <p>The other generations love to pick on us, but the unemployment rate is the lowest it's been in over 50 years</p>
  <div class="more">Read More</div>
</article>
<article class="abs card" style="left:777px">
  <div class="ph" role="img" aria-label="Young entrepreneurs meeting in a cafe" style="background:linear-gradient(135deg,#dfe3e6,#8f9aa0)"></div>
  <div class="icon"><svg width="30" height="30" viewBox="0 0 30 30" fill="none" stroke="#fff" stroke-width="2"><circle cx="15" cy="9" r="5"/><path d="M6 27 V21 Q15 14 24 21 V27"/></svg></div>
  <h3>How To Create Your<br>Own Side Hustle</h3>
  <p>So, you're thinking of starting a side hustle, but before you do you should think about a few things By</p>
  <div class="more">Read More</div>
</article>

<section class="abs band"></section>
<div class="abs frame"></div>
<div class="abs checklist" role="img" aria-label="Dorm &amp; Den and Varsity Purse money matters checklist infographic"></div>
<h2 class="abs" style="left:518px;top:1955px;font-size:43px;font-weight:500;line-height:55px;color:#fff">Why Take A Personal<br>Finance Course?</h2>
<p class="abs" style="left:520px;top:2075px;width:500px;font-size:17.5px;line-height:29px;color:#fff">Varsity Purse will teach you how to use your student loan to get a new car, how to fill out those first day of work tax forms without calling mom and dad,and how to build credit without getting into credit card debt.</p>
<p class="abs" style="left:518px;top:2203px;width:460px;font-size:17.5px;line-height:32px;color:#fff;font-style:italic">"Personal financial skills will keep your wallet full and your options open.Take charge of your finances today!"</p>

<section class="abs resources"></section>
<h2 class="abs section-title serif" style="top:2540px">Our Resources</h2>

<article class="abs post" style="left:93px;top:2630px;width:647px;height:160px">
  <div class="ph" role="img" aria-label="Fanned stack of banknotes" style="width:278px;height:160px;background:linear-gradient(135deg,#8b9683,#3e463a)"></div>
  <div class="date">FEB<br><b>'12</b></div>
  <div class="body" style="left:297px;top:20px;width:335px">
    <h4>How To Create Your Own Side Hustle</h4>
    <div class="meta">by Varsity Purse | May 28, 2019 | How To</div>
    <div class="ex">So, you're thinking of starting a side hustle, but before you do you should think about a few things. By definition, side hustlesare any type of employment</div>
    <div class="rm">Read More</div>
  </div>
</article>
<article class="abs post" style="left:93px;top:2823px;width:647px;height:162px">
  <div class="ph" role="img" aria-label="Traveler reading a map on a city street" style="width:278px;height:162px;background:linear-gradient(135deg,#a78a66,#4a3a2a)"></div>
  <div class="date">FEB<br><b>'10</b></div>
  <div class="body" style="left:297px;top:24px;width:335px">
    <h4 style="letter-spacing:1px">HOW YOU CAN AFFORD TO TRAVEL</h4>
    <div class="meta">by Varsity Purse | May 23, 2019 | How To</div>
    <div class="ex">The memories you make from traveling are priceless, but the travel itself can be pretty pricey. Here are some quick tips that will help you afford to travel no matter your</div>
    <div class="rm">Read More</div>
  </div>
</article>
<article class="abs post" style="left:758px;top:2630px;width:348px;height:365px">
  <div class="ph" role="img" aria-label="Pile of copper and silver coins" style="width:348px;height:172px;background:linear-gradient(135deg,#b4774a,#5a3620)"></div>
  <div class="date">FEB<br><b>'12</b></div>
  <div class="body" style="left:25px;top:198px;width:305px">
    <h4 style="font-size:14px;letter-spacing:1px;line-height:18px">MONEY SAVING HACKS FOR MILLENNIALS</h4>
    <div class="meta">by Varsity Purse | May 28, 2019 | Hacks</div>
    <div class="ex">The other generations love to pick on us, but the unemployment rate is the lowest it's been in over 50 years, so it's good to be a millennial! and already</div>
    <div class="rm">Read More</div>
  </div>
</article>

<h2 class="abs section-title serif" style="top:3175px">Reviews</h2>
<p class="abs sub serif" style="top:3255px">Don't Take Our Word For It...</p>

<div class="abs review" style="left:97px">"Believe it or not, I was fifty before I understood the difference between gross and net profit. Where was Varsity Purse when I needed it?"</div>
<div class="abs review" style="left:446px">"Having personally practiced in the area of personal financial planning for over thirty years, I am thrilled that there is finally a tool that my kids"</div>
<div class="abs review" style="left:796px">"A great course to improve your life in the aspects of financial goals and career services. It opened my eyes to things that I thought I knew,</div>
<div class="abs avatar" role="img" aria-label="Reviewer portrait" style="left:204px"></div>
<div class="abs avatar" role="img" aria-label="Reviewer portrait" style="left:553px"></div>
<div class="abs avatar" role="img" aria-label="Reviewer portrait" style="left:903px;background:linear-gradient(160deg,#c9d3dc,#6f7f8c)"></div>
<div class="abs who" style="left:97px">Dorian Vale<br>Founder of Northwind Ventures</div>
<div class="abs who" style="left:446px">Lena Ostrow<br>Parent</div>
<div class="abs who" style="left:796px">Tobias Reyne<br>College Student</div>
<div class="abs stars" style="left:97px">★★★★★</div>
<div class="abs stars" style="left:446px">★★★★★</div>
<div class="abs stars" style="left:796px">★★★★★</div>

<footer class="abs footer"></footer>
<svg class="abs" style="left:0;top:3728px" width="1200" height="40" viewBox="0 0 1200 40"><path fill="#141414" d="M0 18 L50 24 L110 12 L170 22 L240 14 L300 24 L370 10 L440 20 L510 14 L590 24 L660 12 L720 20 L800 10 L870 22 L940 14 L1010 24 L1080 12 L1140 20 L1200 14 L1200 40 L0 40Z"/></svg>

<h5 class="abs" style="left:90px;top:3890px;color:#fff;font-family:'Montserrat',sans-serif;font-size:20px;font-weight:500">CONTACT US</h5>
<span class="ficon" style="left:90px;top:3940px"></span>
<div class="fitem" style="left:138px;top:3926px;color:#fff;font-family:'Montserrat',sans-serif">Address :<br>41 Linden Row,<br>Fairhaven, OR 97001</div>
<span class="ficon" style="left:90px;top:4015px"></span>
<div class="fitem" style="left:138px;top:4010px;color:#fff;font-family:'Montserrat',sans-serif">Call Us :<br>555 014 2290</div>
<span class="ficon" style="left:90px;top:4080px"></span>
<div class="fitem" style="left:138px;top:4075px;color:#fff;font-family:'Montserrat',sans-serif">E - Mail :<br>hello@varsitypurse.org</div>

<h5 class="abs" style="left:397px;top:3886px;color:#fff;font-family:'Montserrat',sans-serif;font-size:20px;font-weight:500">Quick Links</h5>
<div class="flinks" style="left:397px;top:3922px;color:#fff;font-family:'Montserrat',sans-serif">Home<br>Take The Pledge<br>Blog<br>About Us<br>Tips &amp; Tricks<br>About nuvoe</div>

<h5 class="abs" style="left:640px;top:3886px;color:#fff;font-family:'Montserrat',sans-serif;font-size:20px;font-weight:500">GET IN TOUCH</h5>
<span class="ficon" style="left:638px;top:3930px"></span>
<div class="fitem" style="left:682px;top:3933px;color:#fff;font-family:'Montserrat',sans-serif">Facetome</div>
<span class="ficon" style="left:638px;top:3977px"></span>
<div class="fitem" style="left:682px;top:3980px;color:#fff;font-family:'Montserrat',sans-serif">Chirper</div>
<span class="ficon" style="left:638px;top:4025px"></span>
<div class="fitem" style="left:682px;top:4028px;color:#fff;font-family:'Montserrat',sans-serif">Linkhall</div>
<span class="ficon" style="left:638px;top:4077px"></span>
<div class="fitem" style="left:682px;top:4080px;color:#fff;font-family:'Montserrat',sans-serif">pixolette</div>

<h5 class="abs" style="left:878px;top:3886px;color:#fff;font-family:'Montserrat',sans-serif;font-size:20px;font-weight:500">Newsletter</h5>
<div class="fitem" style="left:878px;top:3926px;width:230px;font-size:15px;line-height:22px;color:#fff;font-family:'Montserrat',sans-serif">Lorem Ipsum has been the industry's standard dummy text ever since the 1500s.</div>
<div class="news-input" style="font-family:'Montserrat',sans-serif">Enter your email address</div>
<div class="news-btn"><svg width="46" height="34" viewBox="0 0 46 34"><path d="M17 17 H29 M25 13 L29 17 L25 21" stroke="#fff" stroke-width="2" fill="none"/></svg></div>

<div class="copyright" style="color:#fff;font-family:'Montserrat',sans-serif">© 2019 Copyrights | All Rights Reserved</div>

</body>
</html>
```